One of a Kind Clean Business Card

We need to design a new business card template for our company. Our company designs and produced merchandising displays. You can see a sample of what we produce on our site www.qorvanexhibits.net. I have uploaded our logo in vector format, as well as a picture of our current business cards. We want a totally different look. We want simple and clean, looking forward to seeing what people create.
Updates

I would like to update the address for Qorvan Display Group Inc. 518 E Tollmere Ln Arlington Heights, IL 60017 Would also note. No QR codes

Industry/Entity Type

Business

Contact Information for Business Card

Need a 1 sided business card designed.

Font styles to use
Serif

Requirements
Must have
• Easy to view; Clean Design
Nice to have
• Features that promote engineering and creativity
Should not have
• Too much clutter, keep it simple

```html
<!DOCTYPE html>
<html lang="en">
<head>
<meta charset="utf-8">
<title>Qorvan Display Group Inc. — Business Card</title>
<link href="https://fonts.googleapis.com/css2?family=Work+Sans:wght@400;600&display=swap" rel="stylesheet">
<style>
  :root {
    --backdrop: #e9e7e4;
    --card: #ffffff;
    --ink: #262626;
    --accent: #7b2a2f;
    --rule: #a0585c;
  }
  * { box-sizing: border-box; margin: 0; padding: 0; }
  html, body {
    width: 1200px; height: 1000px; overflow: hidden;
    background: var(--backdrop);
    font-family: "Work Sans", sans-serif;
    color: var(--ink);
  }
  .business-card {
    position: absolute;
    left: 100px; top: 215px;
    width: 1000px; height: 570px;
    background: var(--card);
    box-shadow: 0 10px 30px rgba(0,0,0,.12);
  }
  .brand {
    position: absolute;
    left: 90px; top: 200px;
    width: 330px;
    display: flex; align-items: center; gap: 14px;
  }
  .brand-mark {
    width: 22px; height: 22px; flex: none;
    background: var(--accent);
  }
  .brand-name {
    font-size: 27px; font-weight: 400; line-height: 1.2;
    color: var(--accent);
    letter-spacing: .01em;
  }
  .divider {
    position: absolute;
    left: 470px; top: 185px;
    width: 2px; height: 150px;
    background: var(--rule);
  }
  .person-name {
    position: absolute;
    left: 500px; top: 128px;
    display: flex; align-items: center; gap: 16px;
    font-size: 38px; font-weight: 600; letter-spacing: .02em;
    text-transform: uppercase;
  }
  .person-name::before {
    content: ""; width: 6px; height: 34px; background: var(--accent);
  }
  .contact-list {
    position: absolute;
    left: 500px; top: 200px;
    list-style: none;
  }
  .contact-list li {
    display: flex; align-items: center; gap: 18px;
    font-size: 24px; line-height: 34px; letter-spacing: .02em;
  }
  .contact-list svg { width: 20px; height: 20px; flex: none; fill: var(--accent); }
  .contact-list .web-domain { color: var(--accent); }
  .address {
    position: absolute;
    left: 0; right: 0; top: 440px;
    text-align: center;
    font-size: 22px; letter-spacing: .02em;
  }
</style>
</head>
<body>
<main class="business-card">
  <div class="brand">
    <span class="brand-mark"></span>
    <span class="brand-name">Qorvan Display Group Inc.</span>
  </div>

  <div class="divider"></div>

  <h1 class="person-name">Dale Vornick</h1>

  <ul class="contact-list">
    <li>
      <svg viewBox="0 0 20 20" aria-hidden="true"><path d="M2 6c0-2 3-3 8-3s8 1 8 3v2h-4V6.5c-1-.5-2.5-.7-4-.7s-3 .2-4 .7V8H2z"/><path d="M4 10h12l1 8H3z"/></svg>
      <span>555-014-8200</span>
    </li>
    <li>
      <svg viewBox="0 0 20 20" aria-hidden="true"><path d="M5 2l3 4-2 2c1 2.5 3 4.5 5.5 5.5l2-2 4 3-1.5 2.5C9 17 3 11 2.5 4.5z"/></svg>
      <span>555-019-0898</span>
    </li>
    <li>
      <svg viewBox="0 0 20 20" aria-hidden="true"><path d="M2 4h16v12H2z"/><path d="M2 4l8 7 8-7" fill="none" stroke="#fff" stroke-width="1.6"/></svg>
      <span>dvornick@qorvanexhibits.net</span>
    </li>
    <li>
      <svg viewBox="0 0 20 20" aria-hidden="true"><circle cx="12" cy="8" r="5.5" fill="none" stroke="#7b2a2f" stroke-width="2.2"/><path d="M8 11.5l-6 6 1.5 1.5 6-6z"/></svg>
      <span>www.<span class="web-domain">qorvanexhibits</span>.net</span>
    </li>
  </ul>

  <p class="address">518 E Tollmere Ln Arlington Heights, IL 60017</p>
</main>
</body>
</html>
```